Heron Property Inspection business card

I am the principal inspector of Heron Property Inspections. I serve Northern Virginia from Winchester to Arlington.Associate, Federated Guild of Dwelling Examiners (FGDE)Graduate, FGDE Home Inspectors CourseNational Association of Home Inspectors ExamI'd like the business card to look more professional than comical.I pulled the attached picture off the web. I'd like to have something like that or an image of a house as my logo on the cards.

Target Market(s)

Persons who recently purchased a home.

Industry/Entity Type

Business

Contact Information for Business Card

Heron Property Inspections, LLC.4455 River RoadBluemont, Virginia 20135cell: 703-231-6680e-mail: tkmarlow@postvale.net

Font styles to use
Serif
Sans Serif

Requirements
Must have
• I'd like to have a logo, something that identifies me as a home inspector. The attached images are something that I'd like to have incorporated into my business card logo.
Nice to have
• I'd like a sketch of a house and/or a magnifying glass showing a house being inspected. The attached images are used as a suggestion only, I do not own the images.
Should not have
• Gimmicky stuff. I want to appear professional and trustworthy.

```html
<!DOCTYPE html>
<html lang="en">
<head>
<meta charset="utf-8">
<title>Heron Property Inspections – Business Card</title>
<link rel="stylesheet" href="https://fonts.googleapis.com/css2?family=Cinzel:wght@500&family=Open+Sans:wght@400;600&display=swap">
<style>
  :root {
    --page-bg: #e9e7e3;
    --card-white: #f7f7f7;
    --brand-blue: #2c5fc4;
    --text-blue: #2a4fb8;
    --text-grey: #6a6a6c;
    --text-white: #ffffff;
  }
  * { margin: 0; padding: 0; box-sizing: border-box; }
  html, body {
    width: 1200px; height: 818px; overflow: hidden;
    background: var(--page-bg);
  }
  .card {
    position: absolute; left: 100px; top: 123px;
    width: 1000px; height: 571px;
    box-shadow: 0 12px 30px rgba(0,0,0,.18);
    overflow: hidden;
  }
  .card-shapes { position: absolute; inset: 0; }
  .card-left {
    position: absolute; left: 56px; top: 0; bottom: 0; width: 330px;
    display: flex; flex-direction: column; justify-content: center; gap: 44px;
  }
  .brand { display: flex; align-items: center; gap: 16px; }
  .brand-dot {
    width: 46px; height: 46px; border-radius: 50%;
    background: var(--brand-blue); flex: none;
  }
  .brand-name {
    font-family: "Cinzel", serif; font-weight: 500;
    color: var(--text-blue);
    font-size: 25px; line-height: 1.2; letter-spacing: .3px;
    white-space: nowrap;
  }
  .person { font-family: "Open Sans", sans-serif; padding-left: 62px; }
  .person-name { color: var(--text-blue); font-weight: 600; font-size: 31px; line-height: 1.15; white-space: nowrap; }
  .person-title { color: var(--text-grey); font-weight: 400; font-size: 22px; margin-top: 4px; white-space: nowrap; }
  .contact {
    position: absolute; right: 50px; top: 150px;
    font-family: "Open Sans", sans-serif; color: var(--text-white);
    font-size: 26px; line-height: 1.5; text-align: right;
  }
  .contact-line { display: flex; justify-content: flex-end; align-items: center; gap: 14px; }
  .contact-icon { width: 26px; height: 22px; flex: none; }
  .icon-spacer { width: 26px; flex: none; }
</style>
</head>
<body>
  <div class="card">
    <svg class="card-shapes" viewBox="0 0 1000 571" width="1000" height="571">
      <defs>
        <linearGradient id="blueFill" x1="0" y1="0" x2="1" y2="1">
          <stop offset="0" stop-color="#3470d6"/>
          <stop offset="1" stop-color="#1f47a3"/>
        </linearGradient>
        <linearGradient id="greyFill" x1="0" y1="0" x2="0" y2="1">
          <stop offset="0" stop-color="#8a8a8c"/>
          <stop offset="1" stop-color="#b9b9bb"/>
        </linearGradient>
      </defs>
      <rect class="card-base" width="1000" height="571" fill="var(--card-white)"/>
      <path class="grey-band" d="M430 0 L575 0 Q450 290 500 571 L470 571 Q400 260 430 0 Z" fill="url(#greyFill)"/>
      <path class="blue-panel" d="M575 0 L1000 0 L1000 571 L500 571 Q450 290 575 0 Z" fill="url(#blueFill)"/>
      <path class="divider-line" d="M575 0 Q450 290 500 571" fill="none" stroke="#ffffff" stroke-width="3"/>
    </svg>

    <div class="card-left">
      <div class="brand">
        <div class="brand-dot"></div>
        <div class="brand-name">Heron Property<br>Inspections, LLC</div>
      </div>
      <div class="person">
        <div class="person-name">Employee Name</div>
        <div class="person-title">Managing Director</div>
      </div>
    </div>

    <div class="contact">
      <div class="contact-line"><span>7182 Quarry Lane</span><span class="icon-spacer"></span></div>
      <div class="contact-line"><span>Fernhill, Virginia 20148</span><span class="icon-spacer"></span></div>
      <div class="contact-line">
        <span>703-555-0192</span>
        <svg class="contact-icon" viewBox="0 0 26 22" aria-label="phone">
          <rect x="7" y="1" width="12" height="20" rx="2" fill="none" stroke="#fff" stroke-width="2"/>
          <rect x="10" y="4" width="6" height="6" fill="#fff"/>
          <circle cx="13" cy="16" r="1.6" fill="#fff"/>
        </svg>
      </div>
      <div class="contact-line">
        <span>tkmarlow@postvale.net</span>
        <svg class="contact-icon" viewBox="0 0 26 22" aria-label="email">
          <rect x="2" y="3" width="22" height="16" fill="none" stroke="#fff" stroke-width="2"/>
          <path d="M2 3 L13 12 L24 3" fill="none" stroke="#fff" stroke-width="2"/>
        </svg>
      </div>
    </div>
  </div>
</body>
</html>
```